Zielgruppe
Verkauf und Einbau von Fenstern, Haustüren, Rollläden, Raffstore, Markisen, Insektenschutzgitter, Plissees
Aufgabenstellung
Es soll das gleiche Farbschema meines Firmenlogos haben. Grauer Hintergrund, kleine gelbe Akzente und schwarze Schrift

```html
<!DOCTYPE html>
<html lang="de">
<head>
<meta charset="utf-8">
<title>Rahmenwerk – Fenster, Haustüren, Sonnenschutz</title>
<link href="https://fonts.googleapis.com/css2?family=Comfortaa:wght@300;400&family=Open+Sans:wght@400;600;700&display=swap" rel="stylesheet">
<style>
:root{
  --yellow:#f6c21b;
  --gray:#9a9a9a;
  --gray-dark:#6f6f6f;
  --panel:#e6e6e6;
  --ink:#222;
  --bar:#3a3a3a;
  --footer:#333;
  --white:#fff;
}
*{box-sizing:border-box;margin:0;padding:0}
html,body{width:1200px;height:4389px;overflow:hidden}
body{font-family:"Open Sans",Arial,sans-serif;color:var(--ink);background:var(--gray);position:relative}
.abs{position:absolute}
.display{font-family:"Comfortaa",Arial,sans-serif;font-weight:300}
.eyebrow{font-size:10px;letter-spacing:4px;color:var(--yellow);text-transform:uppercase;font-weight:600;text-align:center}
.section-title{font-family:"Comfortaa",Arial,sans-serif;font-weight:300;font-size:30px;text-align:center;color:var(--ink)}
.btn{display:inline-flex;align-items:center;justify-content:center;font-size:10px;font-weight:700;text-transform:uppercase;letter-spacing:.3px;height:28px}
.btn-yellow{background:var(--yellow);color:var(--ink)}
.btn-outline{border:1.5px solid var(--white);color:var(--white)}
.btn-outline-dark{border:1.5px solid var(--ink);color:var(--ink)}

/* top bar & hero */
.top-line{left:0;top:0;width:1200px;height:6px;background:var(--yellow);z-index:3}
.hero{left:0;top:0;width:1200px;height:675px;background:linear-gradient(180deg,#2c2620 0%,#4a3b2c 35%,#6a5b4c 60%,#3a332c 100%)}
.brand{left:38px;top:98px;color:var(--yellow);font-size:20px;font-weight:600;letter-spacing:.5px;display:flex;align-items:center;gap:8px}
.brand-square{width:14px;height:14px;background:var(--yellow)}
.nav{right:50px;top:50px;display:flex;gap:16px}
.nav a{font-size:9px;font-weight:700;color:var(--white);text-decoration:none;padding:5px 8px;text-transform:uppercase}
.nav a.active{background:var(--yellow);color:var(--ink)}
.side-actions{right:0;top:133px;width:36px}
.side-actions div{height:36px;background:var(--yellow);border-bottom:1px solid #d8a800;display:flex;align-items:center;justify-content:center}
.hero-arrow{top:322px}
.hero-content{left:0;width:1200px;top:236px;text-align:center;color:var(--white)}
.hero-content .eyebrow{margin-bottom:14px}
.hero-title{font-size:52px;font-weight:400;margin-bottom:16px}
.hero-text{font-size:15px;line-height:24px;margin-bottom:12px}
.hero-buttons{display:flex;gap:6px;justify-content:center}

/* about */
.about-img{width:187px;height:132px;box-shadow:0 3px 8px rgba(0,0,0,.3)}
.about-text{left:641px;top:762px;width:350px}
.about-text .eyebrow{text-align:left;margin-bottom:16px}
.about-text h2{font-size:32px;margin-bottom:14px;color:var(--ink)}
.about-text p{font-size:10px;line-height:14px;color:#444;margin-bottom:14px}
.ticks{list-style:none;font-size:10px;line-height:14.5px;color:#444;margin-bottom:22px}
.ticks li{display:flex;align-items:center;gap:6px}
.ticks li:before{content:"";width:8px;height:8px;border-radius:50%;background:var(--yellow)}

/* contact band */
.band{left:0;top:1122px;width:1200px;height:279px;background:linear-gradient(100deg,#7a7a7a 0%,#c6c6c6 45%,#e2e2e2 70%,#9a9a9a 100%)}
.band-content{left:0;top:1182px;width:1200px;text-align:center;color:var(--white)}
.band-content h2{font-size:30px;line-height:38px;margin:14px 0 14px;font-weight:400}

/* cards */
.tile{width:188px;height:137px;box-shadow:0 3px 8px rgba(0,0,0,.3);background:var(--bar)}
.tile .photo{height:106px}
.tile .label{height:31px;display:flex;align-items:center;justify-content:center;color:var(--white);font-size:12px;font-weight:600}
.tile.active .label{background:var(--yellow);color:var(--ink)}
.p1{background:linear-gradient(135deg,#cfcfcf,#8f7b62)}
.p2{background:linear-gradient(135deg,#2b241d,#8a6a44)}
.p3{background:linear-gradient(135deg,#d8dde2,#3b3f44)}
.p4{background:linear-gradient(135deg,#7fa4c9,#d6d2c6)}
.p5{background:linear-gradient(135deg,#c99d6e,#6d7e55)}
.p6{background:linear-gradient(135deg,#eceff0,#a7b0b6)}
.p7{background:linear-gradient(135deg,#4d4d4d,#a89a85)}
.ask{width:188px;height:137px;background:var(--yellow);box-shadow:0 3px 8px rgba(0,0,0,.3);text-align:center;padding-top:20px}
.ask h3{font-size:13px;font-weight:600;margin-bottom:6px}
.ask p{font-size:9px;line-height:13px;margin-bottom:10px}

/* reviews */
.reviews{left:0;top:1937px;width:1200px;height:537px;background:radial-gradient(ellipse at 50% 40%,#8a8a8a 0%,#5a5a5a 50%,#3a3a3a 100%)}
.review{width:188px;height:130px;background:var(--white);box-shadow:0 3px 8px rgba(0,0,0,.35);padding:14px 12px}
.review-head{display:flex;align-items:center;gap:8px;margin-bottom:6px}
.avatar{width:20px;height:20px;border-radius:50%;background:#cfcfcf}
.review-name{font-size:11px;color:var(--yellow)}
.stars{color:var(--yellow);font-size:12px;letter-spacing:1px;margin-bottom:5px}
.review p{font-size:8.5px;line-height:13px;color:#555}

/* faq */
.faq{left:200px;width:801px}
.faq-item{height:44px;background:var(--bar);color:var(--white);display:flex;align-items:center;justify-content:space-between;padding:0 20px;font-size:17px;margin-bottom:6px}
.faq-item.open{background:var(--yellow);color:var(--ink);margin-bottom:0}
.faq-body{background:var(--white);padding:16px 20px;font-size:9.5px;line-height:14.5px;color:#555;margin-bottom:6px;height:96px}

/* contact */
.contact-lower{left:0;top:3974px;width:1200px;height:367px;background:var(--gray-dark)}
.contact-card{left:200px;top:3761px;width:801px;height:530px;display:flex;box-shadow:0 4px 12px rgba(0,0,0,.25)}
.form-side{width:521px;background:var(--white);padding:42px 37px 0}
.info-side{width:280px;background:var(--panel);padding:42px 32px 0}
.contact-card h2{font-size:21px;margin-bottom:14px;color:var(--ink)}
.intro{font-size:10px;line-height:14px;color:#555;margin-bottom:22px}
.field-label{font-size:9px;color:#444;margin-bottom:4px}
.field-label span{color:#d33}
.field{height:29px;border:1px solid #ccc;margin-bottom:14px;font-size:9px;color:#444;display:flex;align-items:center;justify-content:space-between;padding:0 8px}
.row{display:flex;gap:10px}
.row>div{flex:1}
.textarea{height:62px}
.consent{display:flex;gap:8px;font-size:9px;line-height:13px;color:#555;margin-bottom:20px}
.box{width:10px;height:10px;border:1px solid #aaa;flex:none;margin-top:2px}
.portrait{width:176px;height:176px;border-radius:50%;background:radial-gradient(circle at 50% 45%,#c9b39d 0%,#8f7a66 55%,#4b4a48 100%);margin:10px 0 0 6px}
.address{font-size:10px;line-height:14px;color:#444;margin-top:26px}
.address strong{font-weight:700}
.contact-line{display:flex;align-items:center;gap:8px;font-size:10px;color:#444;margin-top:8px}
.dot{width:12px;height:12px;border-radius:50%;background:var(--yellow);flex:none}

/* chat */
.chat{left:1016px;top:4165px;width:148px;height:126px;background:var(--white);border-radius:6px;box-shadow:0 3px 10px rgba(0,0,0,.3);overflow:hidden}
.chat-head{background:#1f6b5c;height:40px;display:flex;align-items:center;gap:6px;padding:0 8px;color:var(--white);font-size:7px}
.chat-ava{width:20px;height:20px;border-radius:50%;background:#b9a490;flex:none}
.chat-body{background:#ece5dd;height:58px;padding:8px}
.chat-bubble{background:var(--white);border-radius:4px;padding:5px;font-size:6.5px;line-height:9px;width:90px}
.chat-btn{margin:6px 8px;height:14px;border-radius:7px;background:#25a35a;color:var(--white);font-size:6.5px;display:flex;align-items:center;justify-content:center}
.wa{left:1140px;top:4299px;width:22px;height:22px;border-radius:50%;background:#25a35a}

/* footer */
.footer{left:0;top:4341px;width:1200px;height:48px;background:var(--footer);color:#ddd;font-size:9px}
.footer .legal{position:absolute;left:200px;top:19px}
.footer .legal b{color:var(--white)}
.socials{position:absolute;left:653px;top:14px;display:flex;gap:8px}
.socials span{width:22px;height:22px;border-radius:50%;background:var(--yellow)}
.to-top{position:absolute;left:975px;top:12px;width:24px;height:24px;border-radius:50%;background:var(--yellow);display:flex;align-items:center;justify-content:center}
</style>
</head>
<body>

<!-- Hero -->
<div class="abs hero" role="img" aria-label="Moderne Hausfront mit dunkler Haustür, Steinfassade und Pflanzen im Abendlicht"></div>
<div class="abs top-line"></div>
<div class="abs brand"><span class="brand-square"></span>RAHMENWERK</div>
<nav class="abs nav">
  <a class="active">Home</a><a>Über uns</a><a>Leistungen</a><a>Referenzen</a><a>Karriere</a><a>Kontakt</a>
</nav>
<div class="abs side-actions">
  <div><svg width="16" height="16" viewBox="0 0 24 24" fill="none" stroke="#222" stroke-width="2"><path d="M5 3h4l2 5-3 2a11 11 0 0 0 6 6l2-3 5 2v4a2 2 0 0 1-2 2A17 17 0 0 1 3 5a2 2 0 0 1 2-2z"/></svg></div>
  <div><svg width="16" height="16" viewBox="0 0 24 24" fill="none" stroke="#222" stroke-width="2"><rect x="3" y="5" width="18" height="14" rx="1"/><path d="M3 6l9 7 9-7"/></svg></div>
</div>
<svg class="abs hero-arrow" style="left:36px" width="16" height="30" viewBox="0 0 16 30"><path d="M14 2L2 15l12 13" fill="none" stroke="#fff" stroke-width="2"/></svg>
<svg class="abs hero-arrow" style="left:1148px" width="16" height="30" viewBox="0 0 16 30"><path d="M2 2l12 13L2 28" fill="none" stroke="#fff" stroke-width="2"/></svg>
<div class="abs hero-content">
  <div class="eyebrow">Willkommen</div>
  <h1 class="display hero-title">Rahmenwerk</h1>
  <p class="hero-text">Ihr professioneller Partner in allen Fragen rund um Verkauf und Einbau von Fenstern,<br>Haustüren, Rollläden, Raffstore, Markisen, Insektenschutzgitter und Plissees</p>
  <div class="hero-buttons">
    <span class="btn btn-yellow" style="width:128px">Mehr erfahren</span>
    <span class="btn btn-outline" style="width:158px">Kontakt aufnehmen</span>
  </div>
</div>

<!-- About -->
<div class="abs about-img p4" style="left:200px;top:752px" role="img" aria-label="Terrasse mit Raffstore-Anlage"></div>
<div class="abs about-img p2" style="left:404px;top:752px" role="img" aria-label="Haustür bei Abendbeleuchtung"></div>
<div class="abs about-img p7" style="left:200px;top:902px" role="img" aria-label="Innenraum mit Raffstore-Lamellen"></div>
<div class="abs about-img p5" style="left:404px;top:902px" role="img" aria-label="Terrasse mit Markise und Ausblick"></div>
<div class="abs about-text">
  <div class="eyebrow">Rahmenwerk</div>
  <h2 class="display">Wir stellen uns vor</h2>
  <p>Lorem ipsum dolor sit amet, consectetuer adipiscing elit, sed diam nonummy nibh euismod tincidunt ut laoreet dolore magna aliquam erat volutpat. Ut wisi enim ad minim veniam, quis nostrud exerci tation ullamcorper.</p>
  <ul class="ticks">
    <li>Lorem ipsum dolor sit amet consectetuer adipiscing elit esse</li>
    <li>Sed diam nonummy nibh euismod tincidunt</li>
    <li>Laoreet dolore magna aliquam erat volutpat enim ad</li>
    <li>Quis nostrud exerci tation ullamcorper suscipit</li>
    <li>Duis autem vel eum iriure dolor in hendrerit in vulputate</li>
  </ul>
  <span class="btn btn-yellow" style="width:128px">Mehr erfahren</span>
  <span class="btn btn-outline-dark" style="width:159px;margin-left:3px">Kontakt aufnehmen</span>
</div>

<!-- Contact band -->
<div class="abs band" role="img" aria-label="Hand hält ein Smartphone vor hellem Hintergrund"></div>
<div class="abs band-content">
  <div class="eyebrow">Kontakt</div>
  <h2 class="display">Sie haben Fragen?<br>So erreichen Sie uns!</h2>
  <span class="btn btn-yellow" style="width:158px">Kontakt aufnehmen</span>
</div>

<!-- Services -->
<div class="abs eyebrow" style="left:0;top:1476px;width:1200px">Leistungen</div>
<h2 class="abs section-title" style="left:0;top:1506px;width:1200px">Unser Leistungsspektrum im Überblick</h2>
<div class="abs tile active" style="left:200px;top:1570px"><div class="photo p1" role="img" aria-label="Helles Zimmer mit großer Fensterfront"></div><div class="label">Fenster</div></div>
<div class="abs tile" style="left:404px;top:1570px"><div class="photo p2" role="img" aria-label="Dunkle Haustür"></div><div class="label">Haustüren</div></div>
<div class="abs tile" style="left:609px;top:1570px"><div class="photo p3" role="img" aria-label="Geschlossener Rollladen"></div><div class="label">Rollläden</div></div>
<div class="abs tile" style="left:813px;top:1570px"><div class="photo p4" role="img" aria-label="Haus mit Raffstore"></div><div class="label">Raffstore</div></div>
<div class="abs tile" style="left:200px;top:1725px"><div class="photo p5" role="img" aria-label="Terrasse mit Markise"></div><div class="label">Markisen</div></div>
<div class="abs tile" style="left:404px;top:1725px"><div class="photo p6" role="img" aria-label="Fenster mit Insektenschutzgitter"></div><div class="label">Insektenschutzgitter</div></div>
<div class="abs tile" style="left:609px;top:1725px"><div class="photo p7" role="img" aria-label="Fenster mit Plissee"></div><div class="label">Plissees</div></div>
<div class="abs ask" style="left:813px;top:1725px">
  <h3>SIE HABEN FRAGEN?</h3>
  <p>Rufen Sie uns an oder<br>senden Sie uns eine E-Mail.</p>
  <span class="btn btn-outline-dark" style="width:80px;height:24px">Kontakt</span>
</div>

<!-- Reviews -->
<div class="abs reviews" role="img" aria-label="Unscharfe Menschenmenge in Bewegung"></div>
<div class="abs eyebrow" style="left:0;top:2009px;width:1200px">Bewertungen</div>
<h2 class="abs section-title" style="left:0;top:2040px;width:1200px;color:#fff">Das sagen unsere Kunden</h2>
<div class="abs review" style="left:200px;top:2106px"><div class="review-head"><span class="avatar"></span><span class="review-name">Max Mustermann</span></div><div class="stars">★★★★★</div><p>Lorem ipsum dolor sit amet, consectetuer adipiscing elit. Aenean commodo ligula eget dolor. Aenean massa sociis.</p></div>
<div class="abs review" style="left:404px;top:2106px"><div class="review-head"><span class="avatar"></span><span class="review-name">Max Mustermann</span></div><div class="stars">★★★★★</div><p>Lorem ipsum dolor sit amet, consectetuer adipiscing elit. Aenean commodo ligula eget dolor. Aenean massa sociis.</p></div>
<div class="abs review" style="left:609px;top:2106px"><div class="review-head"><span class="avatar"></span><span class="review-name">Max Mustermann</span></div><div class="stars">★★★★★</div><p>Lorem ipsum dolor sit amet, consectetuer adipiscing elit. Aenean commodo ligula eget dolor. Aenean massa sociis.</p></div>
<div class="abs review" style="left:813px;top:2106px"><div class="review-head"><span class="avatar"></span><span class="review-name">Max Mustermann</span></div><div class="stars">★★★★★</div><p>Lorem ipsum dolor sit amet, consectetuer adipiscing elit. Aenean commodo ligula eget dolor. Aenean massa sociis.</p></div>
<div class="abs review" style="left:200px;top:2255px"><div class="review-head"><span class="avatar"></span><span class="review-name">Max Mustermann</span></div><div class="stars">★★★★★</div><p>Lorem ipsum dolor sit amet, consectetuer adipiscing elit. Aenean commodo ligula eget dolor. Aenean massa sociis.</p></div>
<div class="abs review" style="left:404px;top:2255px"><div class="review-head"><span class="avatar"></span><span class="review-name">Max Mustermann</span></div><div class="stars">★★★★★</div><p>Lorem ipsum dolor sit amet, consectetuer adipiscing elit. Aenean commodo ligula eget dolor. Aenean massa sociis.</p></div>
<div class="abs review" style="left:609px;top:2255px"><div class="review-head"><span class="avatar"></span><span class="review-name">Max Mustermann</span></div><div class="stars">★★★★★</div><p>Lorem ipsum dolor sit amet, consectetuer adipiscing elit. Aenean commodo ligula eget dolor. Aenean massa sociis.</p></div>
<div class="abs review" style="left:813px;top:2255px"><div class="review-head"><span class="avatar"></span><span class="review-name">Max Mustermann</span></div><div class="stars">★★★★★</div><p>Lorem ipsum dolor sit amet, consectetuer adipiscing elit. Aenean commodo ligula eget dolor. Aenean massa sociis.</p></div>

<!-- Projects -->
<div class="abs eyebrow" style="left:0;top:2546px;width:1200px">Referenzen</div>
<h2 class="abs section-title" style="left:0;top:2577px;width:1200px">Unsere aktuellen Projekte im Überblick</h2>
<div class="abs tile active" style="left:200px;top:2643px"><div class="photo p1" role="img" aria-label="Projektfoto Fensterfront"></div><div class="label">Projekt 01</div></div>
<div class="abs tile" style="left:404px;top:2643px"><div class="photo p2" role="img" aria-label="Projektfoto Haustür"></div><div class="label">Projekt 02</div></div>
<div class="abs tile" style="left:609px;top:2643px"><div class="photo p3" role="img" aria-label="Projektfoto Rollladen"></div><div class="label">Projekt 03</div></div>
<div class="abs tile" style="left:813px;top:2643px"><div class="photo p4" role="img" aria-label="Projektfoto Raffstore"></div><div class="label">Projekt 04</div></div>
<div class="abs tile" style="left:200px;top:2798px"><div class="photo p5" role="img" aria-label="Projektfoto Markise"></div><div class="label">Projekt 05</div></div>
<div class="abs tile" style="left:404px;top:2798px"><div class="photo p6" role="img" aria-label="Projektfoto Insektenschutz"></div><div class="label">Projekt 06</div></div>
<div class="abs tile" style="left:609px;top:2798px"><div class="photo p7" role="img" aria-label="Projektfoto Plissee"></div><div class="label">Projekt 07</div></div>
<div class="abs tile" style="left:813px;top:2798px"><div class="photo p2" role="img" aria-label="Projektfoto Haustür"></div><div class="label">Projekt 08</div></div>
<div class="abs tile" style="left:200px;top:2953px"><div class="photo p7" role="img" aria-label="Projektfoto Raffstore innen"></div><div class="label">Projekt 09</div></div>
<div class="abs tile" style="left:404px;top:2953px"><div class="photo p4" role="img" aria-label="Projektfoto Hausfassade"></div><div class="label">Projekt 10</div></div>
<div class="abs tile" style="left:609px;top:2953px"><div class="photo p1" role="img" aria-label="Projektfoto Fenster"></div><div class="label">Projekt 11</div></div>
<div class="abs tile" style="left:813px;top:2953px"><div class="photo p5" role="img" aria-label="Projektfoto Terrasse"></div><div class="label">Projekt 12</div></div>

<!-- FAQ -->
<div class="abs eyebrow" style="left:0;top:3237px;width:1200px">FAQ</div>
<h2 class="abs section-title" style="left:0;top:3268px;width:1200px">Häufig gestellte Fragen</h2>
<div class="abs faq" style="top:3333px">
  <div class="faq-item open">Blindtextfrage 01<svg width="16" height="10" viewBox="0 0 16 10"><path d="M1 9l7-7 7 7" fill="none" stroke="#fff" stroke-width="1.6"/></svg></div>
  <div class="faq-body">Lorem ipsum dolor sit amet, consectetuer adipiscing elit. Aenean commodo ligula eget dolor. Aenean massa. Cum sociis natoque penatibus et magnis dis parturient montes, nascetur ridiculus mus. Donec quam felis, ultricies nec, pellentesque eu, pretium quis, sem. Nulla consequat massa quis enim. Donec pede justo, fringilla vel, aliquet nec, vulputate eget, arcu. In enim justo, rhoncus ut, imperdiet a, venenatis vitae, justo. Nullam dictum felis eu pede mollis pretium. Integer tincidunt. Cras dapibus elementum semper nisi. Aenean vulputate eleifend tellus. Aenean leo ligula varius laoreet. Sed fringilla mauris sit sodales dis parturient montes, nascetur ridiculus mus.</div>
  <div class="faq-item">Blindtextfrage 02<svg width="16" height="10" viewBox="0 0 16 10"><path d="M1 1l7 7 7-7" fill="none" stroke="#fff" stroke-width="1.6"/></svg></div>
  <div class="faq-item">Blindtextfrage 03<svg width="16" height="10" viewBox="0 0 16 10"><path d="M1 1l7 7 7-7" fill="none" stroke="#fff" stroke-width="1.6"/></svg></div>
  <div class="faq-item">Blindtextfrage 04<svg width="16" height="10" viewBox="0 0 16 10"><path d="M1 1l7 7 7-7" fill="none" stroke="#fff" stroke-width="1.6"/></svg></div>
  <div class="faq-item">Blindtextfrage 05<svg width="16" height="10" viewBox="0 0 16 10"><path d="M1 1l7 7 7-7" fill="none" stroke="#fff" stroke-width="1.6"/></svg></div>
</div>

<!-- Contact -->
<div class="abs contact-lower"></div>
<div class="abs contact-card">
  <div class="form-side">
    <h2 class="display">Kontaktformular</h2>
    <p class="intro">Lorem ipsum dolor sit amet, consectetueradipis Aenean comcommodo<br>ligula eget dolor Quisque rutrum Aenean imperd Maecenas nec odio.</p>
    <div class="field-label">Anrede <span>*</span></div>
    <div class="field">Herr<svg width="10" height="6" viewBox="0 0 10 6"><path d="M1 1l4 4 4-4" fill="none" stroke="#444"/></svg></div>
    <div class="row">
      <div><div class="field-label">Vorname <span>*</span></div><div class="field"></div></div>
      <div><div class="field-label">Nachname <span>*</span></div><div class="field"></div></div>
    </div>
    <div class="row">
      <div><div class="field-label">Telefon <span>*</span></div><div class="field"></div></div>
      <div><div class="field-label">E-Mail <span>*</span></div><div class="field"></div></div>
    </div>
    <div class="field-label">Nachricht <span>*</span></div>
    <div class="field textarea"></div>
    <div class="consent"><span class="box"></span><span>Ich erkläre mich mit der Verarbeitung der eingegebenen Daten<br>sowie der Datenschutzerklärung einverstanden. <span style="color:#d33">*</span></span></div>
    <span class="btn btn-yellow" style="width:130px">Anfrage senden</span>
  </div>
  <div class="info-side">
    <h2 class="display">Kontakt</h2>
    <p class="intro" style="margin-bottom:0">Lorem ipsum dolor sit amet, consectetuer Aenean comcommodo ligula eget dolor.</p>
    <div class="portrait" role="img" aria-label="Porträtfoto des Ansprechpartners"></div>
    <p class="address"><strong>Rahmenwerk</strong><br>Konrad Falter<br>Lindenweg 7<br>23900 Musterstadt</p>
    <div class="contact-line" style="margin-top:14px"><span class="dot"></span>+49 4100 552107</div>
    <div class="contact-line"><span class="dot"></span>+49 170 55 48 21</div>
    <div class="contact-line"><span class="dot"></span>kfalter@rahmenwerk-nord.de</div>
  </div>
</div>

<!-- Chat -->
<div class="abs chat">
  <div class="chat-head"><span class="chat-ava"></span><span><b>Lena Hart</b><br>Antwortet meist sofort</span></div>
  <div class="chat-body"><div class="chat-bubble"><b>Lena Hart</b><br>Hallo 👋<br>Wie kann ich Ihnen helfen?</div></div>
  <div class="chat-btn">Chat starten</div>
</div>
<div class="abs wa"></div>

<!-- Footer -->
<footer class="abs footer">
  <div class="legal">© 2024 | <b>RAHMENWERK</b> | Impressum | Datenschutz | AGB</div>
  <div class="socials"><span></span><span></span><span></span><span></span></div>
  <div class="to-top"><svg width="12" height="8" viewBox="0 0 12 8"><path d="M1 7l5-5 5 5" fill="none" stroke="#222" stroke-width="2"/></svg></div>
</footer>

</body>
</html>
```